The Brandwell Firm

We need a new design for our letterhead and envelopes. We are a personal injury and criminal defense firm so we need something modern and clean, but more on the professional/traditional side. Our new logo has two colors and is attached to the file so we need something that works well with those colors/matches the design. The following information needs to be on the letterhead:
Phone: (555) 214-3370
Fax: (555) 214-5186
Toll-Free: (888) 431-2059
Post Office Box 4721
Millbrook, SC 29555-4721
HarmClaimCounsel.example
PalmettoTrialAdvocates.example

Target Market(s)

Clients, government agencies, other law firms

Industry/Entity Type

Legal

Font styles to use
Sans Serif
Other font styles liked:
• Arial

Colors

Designer to choose colors to be used in the design.

Requirements
Must have
• Must look professional and clean, modern
Nice to have
• I would like to see a design that works with the logo but does not distract from the content that will be printed on it
Should not have
• Too many colors or crazy designs.

```html
<!DOCTYPE html>
<html lang="en">
<head>
<meta charset="utf-8">
<title>The Brandwell Firm — Stationery</title>
<link href="https://fonts.googleapis.com/css2?family=Open+Sans:wght@400;600;700&display=swap" rel="stylesheet">
<style>
  :root {
    --navy: #2e3192;
    --red: #d71f26;
    --ink: #333333;
    --paper: #ffffff;
    --backdrop: #e6e6e6;
    --faint: #f3eef4;
  }
  * { margin: 0; padding: 0; box-sizing: border-box; }
  html, body { width: 1200px; height: 1200px; overflow: hidden; }
  body {
    background: var(--backdrop);
    font-family: "Open Sans", Arial, sans-serif;
    color: var(--ink);
    position: relative;
  }
  .piece { position: absolute; background: var(--paper); overflow: hidden; }
  .brand-bars { position: absolute; left: 0; right: 0; height: 6px; display: flex; gap: 2px; }
  .brand-bars .navy { background: var(--navy); flex: 0 0 67%; }
  .brand-bars .red { background: var(--red); flex: 1; }
  .brand-bars.top { top: 0; }
  .brand-bars.bottom { bottom: 0; }

  .wordmark {
    position: absolute;
    display: flex; align-items: center; gap: 6px;
    font-weight: 700; color: var(--navy); white-space: nowrap;
    letter-spacing: 0.02em;
  }
  .wordmark .dot { border-radius: 50%; background: var(--red); flex: none; }
  .wordmark.light { color: var(--paper); }
  .wordmark.light .dot { background: var(--paper); }

  .faint-mark {
    position: absolute; border-radius: 50%; background: var(--faint);
  }

  /* Letterhead */
  .letterhead { left: 175px; top: 210px; width: 391px; height: 544px; }
  .letterhead .wordmark { left: 20px; top: 72px; font-size: 13px; }
  .letterhead .wordmark .dot { width: 10px; height: 10px; }
  .contact-block {
    position: absolute; left: 264px; top: 30px;
    border-left: 1px solid var(--navy); padding-left: 7px;
    font-size: 6px; line-height: 8.3px;
  }
  .contact-block .address { margin-bottom: 2px; }
  .contact-line { display: flex; align-items: center; gap: 3px; }
  .contact-line svg { width: 5px; height: 5px; fill: var(--red); flex: none; }
  .letter {
    position: absolute; left: 44px; top: 158px; width: 305px;
    font-size: 6.6px; line-height: 11.8px; color: #222;
  }
  .letter p { margin-bottom: 11.5px; text-align: justify; }
  .letter .salutation { margin-bottom: 12px; }
  .signature { width: 42px; height: 22px; background: linear-gradient(90deg, #e9e9ee, #f6f6f8); margin-top: 24px; }
  .signer-name { font-size: 9px; margin-top: 10px; }
  .signer-title { font-size: 6.5px; margin-top: 6px; }
  .letterhead .faint-mark { left: 325px; top: 440px; width: 110px; height: 110px; }

  /* Cover sheet */
  .cover { left: 622px; top: 185px; width: 460px; height: 576px; }
  .cover .wordmark { left: 0; right: 0; top: 262px; justify-content: center; font-size: 28px; gap: 12px; }
  .cover .wordmark .dot { width: 22px; height: 22px; }
  .cover .faint-mark { left: 350px; top: 440px; width: 140px; height: 140px; }

  /* Business cards */
  .card-front { left: 41px; top: 798px; width: 176px; height: 101px; }
  .card-front .wordmark { left: 10px; top: 22px; font-size: 7px; gap: 3px; }
  .card-front .wordmark .dot { width: 6px; height: 6px; }
  .card-person { position: absolute; right: 11px; top: 56px; text-align: right; }
  .card-person .name { font-size: 6.5px; font-weight: 700; color: var(--red); letter-spacing: 0.04em; }
  .card-person .role { font-size: 3.6px; font-weight: 600; color: var(--navy); }
  .card-rule { position: absolute; left: 10px; right: 11px; top: 63.5px; height: 0.6px; background: #999; }
  .card-contacts { position: absolute; left: 10px; top: 68px; font-size: 3.8px; line-height: 5.3px; }
  .card-contacts .contact-line svg { width: 3.4px; height: 3.4px; }
  .card-address { position: absolute; right: 11px; top: 80px; font-size: 3.8px; line-height: 5px; text-align: right; }
  .card-front .brand-bars { height: 4px; }

  .card-back { left: 41px; top: 922px; width: 175px; height: 100px; background: var(--navy); }
  .card-back .wordmark { left: 0; right: 0; top: 44px; justify-content: center; font-size: 10px; gap: 4px; }
  .card-back .wordmark .dot { width: 8px; height: 8px; }
  .card-back .faint-mark { left: 125px; top: 8px; width: 70px; height: 70px; background: rgba(255,255,255,0.08); }

  /* Envelope front */
  .envelope-front { left: 254px; top: 813px; width: 431px; height: 204px; }
  .envelope-front .wordmark { left: 18px; top: 54px; font-size: 13px; }
  .envelope-front .wordmark .dot { width: 10px; height: 10px; }
  .envelope-front .faint-mark { left: 330px; top: 60px; width: 110px; height: 110px; }
  .return-address { position: absolute; left: 18px; top: 163px; font-size: 6px; line-height: 8px; }
  .return-address .web { color: var(--red); font-weight: 600; font-size: 6.5px; }

  /* Envelope back */
  .envelope-back { left: 722px; top: 813px; width: 431px; height: 204px; }
  .envelope-back .flap { position: absolute; left: 0; top: 0; width: 431px; height: 58px; }
  .envelope-back .flap-mark { position: absolute; left: 209px; top: 14px; width: 13px; height: 13px; border-radius: 50%; background: var(--paper); }
</style>
</head>
<body>
<svg width="0" height="0" style="position:absolute" aria-hidden="true">
  <defs>
    <symbol id="icon-phone" viewBox="0 0 10 10"><path d="M2 0.5 L4 0.5 L4.6 3 L3.3 3.9 Q4.3 5.9 6.1 6.8 L7 5.5 L9.5 6.1 L9.5 8.1 Q9.5 9.5 8 9.5 Q1 9 0.5 2 Q0.5 0.5 2 0.5Z"/></symbol>
    <symbol id="icon-fax" viewBox="0 0 10 10"><path d="M2.5 0.5h5v2.5h-5z M0.5 3.5h9v4h-1.5v-1.5h-6v1.5h-1.5z M2.5 6.5h5v3h-5z"/></symbol>
    <symbol id="icon-web" viewBox="0 0 10 10"><path d="M5 0.5a4.5 4.5 0 1 0 0.01 0z M5 1.6a3.4 3.4 0 1 1-0.01 0z M4.4 1.2h1.2v7.6h-1.2z M1 4.4h8v1.2h-8z"/></symbol>
  </defs>
</svg>

<!-- Letterhead -->
<section class="piece letterhead">
  <div class="brand-bars top"><span class="navy"></span><span class="red"></span></div>
  <div class="wordmark"><span class="dot"></span>The Brandwell Firm</div>
  <div class="contact-block">
    <div class="address">Post Office Box 4721<br>Millbrook, SC 29555-4721</div>
    <div class="contact-line"><svg><use href="#icon-phone"/></svg>(555) 214-3370</div>
    <div class="contact-line"><svg><use href="#icon-fax"/></svg>(555) 214-5186</div>
    <div class="contact-line"><svg><use href="#icon-phone"/></svg>(888) 431-2059 (Toll-Free)</div>
    <div class="contact-line"><svg><use href="#icon-web"/></svg>HarmClaimCounsel.example</div>
    <div class="contact-line"><svg><use href="#icon-web"/></svg>PalmettoTrialAdvocates.example</div>
  </div>
  <div class="letter">
    <p class="salutation">Dear Mr. Carter,</p>
    <p>Lorem ipsum dolor sit amet, consectetur adipiscing elit. Donec orci purus, luctus vitae dignissim eu, iaculis sed purus. Vivamus faucibus, ipsum nec aliquet viverra, leo mauris condimentum ligula, sit amet sagittis enim ligula quis arcu. Nam egestas tortor id nisi porttitor mattis. In tortor ante, ultricies in suscipit a, tempus non massa. Vivamus et auctor mi. Fusce vel massa nulla. Phasellus nec eros mauris, et scelerisque orci. Donec malesuada orci vitae nulla accumsan porta a id massa. Quisque accumsan iaculis magna sit amet fringilla. Maecenas consequat, magna eget tincidunt semper, odio nibh rutrum mi, id feugiat ante nisi eu risus. Vestibulum nunc orci, rhoncus a placerat in, ultricies in mi. Cras mattis varius eros, vel fringilla nisi suscipit eget.</p>
    <p>Quisque scelerisque sagittis nulla at porttitor. Mauris a justo et tellus interdum tristique. Sed id augue vitae urna euismod commodo aliquet a quam. Pellentesque arcu velit, cursus et malesuada ut, consequat et diam. Nullam erat sem, rhoncus id ullamcorper vitae, rhoncus et arcu. In ultricies ultricies nulla, ut rutrum nisi iaculis at. Donec eu magna a metus ornare faucibus. Fusce aliquet faucibus ultricies. Morbi semper, est id tincidunt gravida, sem arcu adipiscing lacus, ac bibendum nulla leo eu purus. Quisque nec diam sed risus consectetur a ccumsan quis quis nibh. Vestibulum id purus lorem.</p>
    <div class="signature" role="img" aria-label="Handwritten signature"></div>
    <div class="signer-name">Daniel Reyes</div>
    <div class="signer-title">Co-Founder &amp; CEO</div>
  </div>
  <div class="faint-mark"></div>
</section>

<!-- Cover sheet -->
<section class="piece cover">
  <div class="brand-bars top"><span class="navy"></span><span class="red"></span></div>
  <div class="wordmark"><span class="dot"></span>The Brandwell Firm</div>
  <div class="faint-mark"></div>
</section>

<!-- Business card front -->
<section class="piece card-front">
  <div class="wordmark"><span class="dot"></span>The Brandwell Firm</div>
  <div class="card-person">
    <div class="name">ADRIAN HOLT</div>
    <div class="role">Attorney at Law</div>
  </div>
  <div class="card-rule"></div>
  <div class="card-contacts">
    <div class="contact-line"><svg><use href="#icon-phone"/></svg>(555) 214-3370</div>
    <div class="contact-line"><svg><use href="#icon-fax"/></svg>(555) 214-5186</div>
    <div class="contact-line"><svg><use href="#icon-phone"/></svg>(888) 431-2059 (Toll-Free)</div>
    <div class="contact-line"><svg><use href="#icon-web"/></svg>HarmClaimCounsel.example</div>
    <div class="contact-line"><svg><use href="#icon-web"/></svg>PalmettoTrialAdvocates.example</div>
  </div>
  <div class="card-address">Post Office Box 4721<br>Millbrook, SC 29555-4721</div>
  <div class="brand-bars bottom"><span class="navy"></span><span class="red"></span></div>
</section>

<!-- Business card back -->
<section class="piece card-back">
  <div class="faint-mark"></div>
  <div class="wordmark light"><span class="dot"></span>The Brandwell Firm</div>
</section>

<!-- Envelope front -->
<section class="piece envelope-front">
  <div class="wordmark"><span class="dot"></span>The Brandwell Firm</div>
  <div class="faint-mark"></div>
  <div class="return-address">
    Post Office Box 4721<br>Millbrook, SC 29555-4721<br>
    <span class="web">HarmClaimCounsel.example</span>
  </div>
  <div class="brand-bars bottom"><span class="navy"></span><span class="red"></span></div>
</section>

<!-- Envelope back -->
<section class="piece envelope-back">
  <svg class="flap" viewBox="0 0 431 58" aria-hidden="true">
    <path d="M0 0 H431 L424 44 Q422 56 408 56 H23 Q9 56 7 44 Z" fill="var(--navy)"/>
  </svg>
  <div class="flap-mark"></div>
</section>
</body>
</html>
```